Business card for Luxury Portable Restroom Trailer company

We are a Luxury Portable Restroom Trailer Company Called FALCRIDGE HIRES. Based in Orange County California. We provide portable restroom trailers for events, such as, Weddings, Concerts, Charity events, Sporting events, Tournaments, Corporate events, ect. We rent and Sell the Luxury restrooms. Our colors are white, grey, and Orange. As you will see in the logo we uploaded.
There are 2 people in the company so the names and titles will change for the 3 people but card will remain the same. Here is the information for each Person: Dwight Penner CFO 555 318-0476
next Person: Leon Marchetti VP 555 318-0476
Next Person: Owen Marchetti CEO 555 318-0476
Information to include on the card: Luxury Restroom Trailers Rental and Sales. Weddings, Concerts, Charity, Sporting and Corp. Events.

```html
<!DOCTYPE html>
<html lang="en">
<head>
<meta charset="utf-8">
<title>Falcridge Hires – Business Card</title>
<link rel="stylesheet" href="https://fonts.googleapis.com/css2?family=Montserrat:wght@400;700&family=Open+Sans:wght@400&display=swap">
<style>
  :root {
    --orange: #f06a25;
    --orange-light: #f5935c;
    --orange-dark: #e65c18;
    --grey-text: #5f5f5f;
    --grey-dark: #4a4a4a;
    --card-white: #f3f3f3;
    --backdrop: #d9d9d9;
  }
  * { margin: 0; padding: 0; box-sizing: border-box; }
  html, body {
    width: 1200px; height: 1200px; overflow: hidden;
    background: var(--backdrop);
  }
  .canvas {
    position: relative; width: 1200px; height: 1200px;
  }
  .card {
    position: absolute; left: 150px; width: 900px; height: 500px;
    border-radius: 28px; overflow: hidden;
    box-shadow: 0 6px 18px rgba(0,0,0,0.18);
  }
  /* Back side */
  .card--back { top: 70px; }
  .back-pattern {
    position: absolute; inset: 0;
    background: linear-gradient(100deg, var(--orange-light) 0%, var(--orange) 55%, var(--orange-dark) 100%);
  }
  .back-brand {
    position: absolute; right: 110px; top: 220px;
    display: flex; align-items: center; gap: 14px;
  }
  .back-brand__dot {
    width: 64px; height: 64px; border-radius: 50%;
    border: 5px solid #fff;
  }
  .back-brand__name {
    font-family: "Montserrat", sans-serif; font-weight: 700;
    font-size: 22px; color: #fff; letter-spacing: 1px;
  }
  /* Front side */
  .card--front { top: 630px; background: var(--card-white); }
  .front-brand {
    position: absolute; right: 70px; top: 60px;
    font-family: "Montserrat", sans-serif; font-weight: 700;
    font-size: 38px; color: var(--orange); letter-spacing: 1px;
  }
  .person { position: absolute; left: 70px; top: 75px; }
  .person__name {
    font-family: "Montserrat", sans-serif; font-weight: 700;
    font-size: 46px; color: var(--orange);
  }
  .person__title {
    font-family: "Montserrat", sans-serif; font-weight: 400;
    font-size: 24px; color: var(--grey-text); margin-top: 8px; margin-left: 14px;
  }
  .address {
    position: absolute; left: 110px; top: 290px;
    font-family: "Montserrat", sans-serif; font-size: 24px;
    line-height: 1.3; color: var(--grey-text);
  }
  .contacts {
    position: absolute; left: 110px; top: 370px; list-style: none;
    font-family: "Montserrat", sans-serif; font-size: 24px; color: var(--grey-text);
  }
  .contacts li { display: flex; align-items: center; gap: 14px; height: 34px; }
  .contacts svg { width: 20px; height: 20px; fill: var(--orange); }
  .services {
    position: absolute; right: 70px; top: 300px; text-align: right;
    font-family: "Open Sans", sans-serif; font-size: 21px;
    line-height: 1.55; color: var(--grey-dark);
  }
</style>
</head>
<body>
<main class="canvas">
  <section class="card card--back">
    <div class="back-pattern" role="img" aria-label="Orange background with a repeated embossed brand pattern"></div>
    <div class="back-brand">
      <span class="back-brand__dot"></span>
      <span class="back-brand__name">FALCRIDGE HIRES</span>
    </div>
  </section>

  <section class="card card--front">
    <div class="front-brand">FALCRIDGE HIRES</div>
    <div class="person">
      <h1 class="person__name">Dwight Penner</h1>
      <p class="person__title">CFO</p>
    </div>
    <p class="address">4180 Harlow Lane<br>Brookvale Maine 04127</p>
    <ul class="contacts">
      <li>
        <svg viewBox="0 0 24 24" aria-hidden="true"><path d="M6.6 10.8a15.1 15.1 0 0 0 6.6 6.6l2.2-2.2a1 1 0 0 1 1-.25 11.4 11.4 0 0 0 3.6.57 1 1 0 0 1 1 1V20a1 1 0 0 1-1 1A17 17 0 0 1 3 4a1 1 0 0 1 1-1h3.5a1 1 0 0 1 1 1c0 1.25.2 2.45.57 3.6a1 1 0 0 1-.25 1z"/></svg>
        555 318-0476
      </li>
      <li>
        <svg viewBox="0 0 24 24" aria-hidden="true"><path d="M2 5h20v14H2z M2 5l10 8 10-8" stroke="#fff" stroke-width="1.5"/></svg>
        info@falcridgehires.com
      </li>
      <li>
        <svg viewBox="0 0 24 24" aria-hidden="true"><circle cx="12" cy="12" r="10"/><path d="M2 12h20M12 2c3 3 3 17 0 20M12 2c-3 3-3 17 0 20" stroke="#fff" stroke-width="1.5" fill="none"/></svg>
        www.falcridgehires.com
      </li>
    </ul>
    <p class="services">
      Luxury Restroom, Trailers Rental and Sales,<br>
      Weddings, Concerts, Charity,<br>
      Sporting and Corp. Events
    </p>
  </section>
</main>
</body>
</html>
```